Professional, Attractive, Simple Website Needed!!

We completed the design for our logo.

We need a website built out around this.

Here are a couple samples of how we want ours formatted.

http://brimvoltco.com

http://www.ravelbeam.com/lp/free-quote?LeadSource=Search%20Engine&ProgramName=searchads&experience=qual&language=en&type=brd&gclid=Xk7PLmqwTRZBNVuEYcaHdFgWsLoPeRtQnMxVbCzJaKiOuYtReWqAsDfGhJkLzXcVbNmQwErTyUiOpAsDfGhJkLzX_wcB

http://quorel.co
Updates

Project Deadline Extended
Reason: Extending this deadline due to our delay in providing designers with content for each page. This is coming in next 24 hours.

Project Deadline Extended
Reason: Due to scheduling conflicts and extended travel delays related to Puerto Rico, the deadline has been extended. Your patience is greatly appreciated.

Project Deadline Extended
Reason: Travel and scheduling conflicts have made it impossible to give this project the thorough review it deserves, therefore I am extending the deadline. Thank you for your patience!

Target Market(s)

Home Owners who earn 60k + household annually

Industry/Entity Type

It Professional

Coding

Coded - Design and coding required

Number of Pages Required

5+ page

Font styles to use
Serif

Colors
34a7d8
9bcb3c

Requirements
Must have
• Simple
• Lead form Entry (Ability for visitor to enter Name, number and address for a quote)
• Sleek Design
• Professional
• Testimonials
• Use color Scheme of Design Logo Attached
Nice to have
• Video when site starts
• Like this
• https://www.vidplexa.com/watch?v=Qm8rTbLw3Np&feature=vidplexa.be
Should not have
• Should not include Commercial solar
• Should not include wind power

```html
<!DOCTYPE html>
<html lang="en">
<head>
<meta charset="utf-8">
<title>Brightfield Energy</title>
<link href="https://fonts.googleapis.com/css2?family=Open+Sans:ital,wght@0,400;0,600;0,700;1,400&display=swap" rel="stylesheet">
<style>
:root{
  --green:#8dc63f;
  --green-dark:#7ab32e;
  --blue:#1e88c9;
  --blue-dark:#1576b3;
  --white:#ffffff;
  --grey-bg:#f0f0f0;
  --ink:#222222;
  --muted:#666666;
  --footer:#232323;
  --footer-line:#3a3a3a;
  --link:#2a8fd0;
}
*{box-sizing:border-box;margin:0;padding:0}
html,body{width:1200px;height:3309px;overflow:hidden}
body{position:relative;font-family:"Open Sans",Arial,sans-serif;color:var(--ink);background:var(--white)}
.section{position:absolute;left:0;width:1200px}

/* Hero */
.hero{top:0;height:630px;z-index:2;clip-path:path('M0 0H1200V570Q600 660 0 570Z')}
.hero-photo{position:absolute;inset:0;background:
  radial-gradient(ellipse 260px 380px at 960px 300px,rgba(232,120,40,.55),transparent 70%),
  linear-gradient(180deg,#7fa7cf 0%,#a9c2da 18%,#3d5a80 30%,#243a5c 60%,#1b2c45 100%)}
.hero-shade{position:absolute;inset:0;background:rgba(10,20,35,.25)}
.nav{position:absolute;top:0;left:0;width:1200px;height:118px}
.logo{position:absolute;left:92px;top:40px;display:flex;align-items:center;gap:8px}
.logo-mark{width:40px;height:40px;border-radius:50%;background:var(--green)}
.logo-name{font-size:17px;font-weight:700;color:var(--white);letter-spacing:.5px}
.nav-links{position:absolute;top:50px;left:440px;display:flex;align-items:center;font-size:16px}
.nav-links a{color:var(--white);text-decoration:none;position:absolute;white-space:nowrap}
.nav-links a.active{color:var(--green)}
.btn-login{position:absolute;left:508px;top:-6px;width:82px;height:32px;border-radius:16px;background:var(--green);color:var(--white);font-size:16px;display:flex;align-items:center;justify-content:center}
.social{position:absolute;top:50px;left:1050px;display:flex;gap:10px}
.social span{width:22px;height:22px;border-radius:50%;background:var(--white);display:block}
.nav-rule{position:absolute;left:440px;top:116px;width:670px;height:1px;background:rgba(255,255,255,.45)}
.play{position:absolute;left:566px;top:254px;width:68px;height:68px;border-radius:50%;background:rgba(20,20,20,.7);border:2px solid rgba(255,255,255,.5)}
.play svg{position:absolute;left:24px;top:20px}
.hero-title{position:absolute;top:350px;width:1200px;text-align:center;color:var(--white);font-size:54px;font-weight:400}
.hero-sub{position:absolute;top:425px;width:1200px;text-align:center;color:var(--white);font-size:24px}
.dots{position:absolute;top:597px;left:568px;display:flex;gap:6px}
.dots span{width:9px;height:9px;border-radius:50%;background:var(--white)}
.dots span.on{background:var(--green)}

/* Services */
.services{top:540px;height:700px;z-index:1;background:var(--green)}
.section-title{position:absolute;width:1200px;text-align:center;font-size:34px;font-weight:400}
.services .section-title{top:168px;color:var(--white)}
.service{position:absolute;top:267px;width:290px;text-align:center;color:var(--white)}
.service-icon{width:116px;height:116px;margin:0 auto;border-radius:50%;border:3px solid rgba(255,255,255,.85);padding:6px}
.service-icon div{width:100%;height:100%;border-radius:50%;background:var(--white);display:flex;align-items:center;justify-content:center}
.service h3{font-size:22px;font-weight:400;margin-top:24px}
.service p{font-size:13px;line-height:22px;margin-top:10px}

/* About */
.about{top:1080px;height:520px;z-index:3;background:var(--white);clip-path:path('M0 90Q600 -10 1200 90V520H0Z')}
.about-frame{position:absolute;left:161px;top:140px;width:330px;height:270px;background:var(--blue)}
.about-photo{position:absolute;left:181px;top:150px;width:333px;height:286px;background:linear-gradient(180deg,#9cc2e0 0%,#cfe0ea 35%,#5f8b4a 55%,#34567d 70%,#22395a 100%);box-shadow:0 10px 22px rgba(0,0,0,.25)}
.about-title{position:absolute;left:565px;top:168px;font-size:34px;font-weight:400}
.about-text{position:absolute;left:565px;top:222px;width:500px;font-size:13.5px;line-height:23.5px;color:var(--muted)}
.btn-more{position:absolute;left:565px;top:390px;width:105px;height:30px;border-radius:15px;background:var(--green);color:var(--white);font-size:13px;font-weight:600;display:flex;align-items:center;justify-content:center}

/* What we do */
.work{top:1520px;height:720px;z-index:4;background:var(--grey-bg);clip-path:path('M0 0Q600 120 1200 0V720H0Z')}
.work .section-title{top:180px}
.card{position:absolute;top:274px;height:292px;background:var(--white);box-shadow:0 3px 8px rgba(0,0,0,.15);text-align:center}
.card-photo{height:168px}
.card h3{font-size:18px;font-weight:400;margin-top:20px}
.card p{font-size:13px;line-height:22px;color:var(--muted);margin:6px 18px 0}
.card a{display:block;font-size:12.5px;color:var(--link);text-decoration:none;margin-top:4px}

/* Testimonials */
.testimonials{top:2160px;height:520px;z-index:5;background:var(--white);clip-path:path('M0 40Q600 -20 1200 40V520H0Z')}
.testimonials .section-title{top:102px}
.quote{position:absolute;left:240px;top:185px;width:720px;text-align:center;font-size:17px;line-height:30px;color:#555}
.qmark{color:var(--blue);font-weight:700;font-size:22px}
.avatar{position:absolute;left:554px;top:280px;width:92px;height:92px;border-radius:50%;background:linear-gradient(180deg,#d9dde2,#8a95a3)}
.arrow{position:absolute;top:310px}
.author{position:absolute;top:390px;width:1200px;text-align:center;font-style:italic;font-size:16px;color:#444}

/* Contact */
.contact{top:2605px;height:450px;z-index:6;background:var(--blue);clip-path:path('M0 0Q600 90 1200 0V450H0Z')}
.contact .section-title{top:112px;color:var(--white)}
.field{position:absolute;top:203px;width:292px;height:58px;background:var(--white);border-radius:3px;font-size:16px;color:#555;padding:18px 14px}
.btn-submit{position:absolute;left:516px;top:292px;width:168px;height:44px;border-radius:22px;background:var(--green);color:var(--white);font-size:22px;display:flex;align-items:center;justify-content:center}

/* Footer */
.footer{top:2950px;height:359px;z-index:7;background:var(--footer);clip-path:path('M0 0Q600 110 1200 0V359H0Z');color:var(--white)}
.f-col{position:absolute;top:113px}
.f-col h4{font-size:16px;font-weight:400;margin-bottom:18px}
.f-col li{list-style:none;font-size:12.5px;line-height:24px;display:flex;align-items:center;gap:7px}
.f-social{display:flex;gap:8px;margin-bottom:12px}
.f-social span{width:24px;height:24px;border-radius:50%;background:var(--white)}
.f-note{font-size:12.5px;line-height:18px;width:260px}
.f-sub{display:flex;margin-top:12px}
.f-sub div{height:30px;font-size:11.5px;display:flex;align-items:center;padding:0 8px}
.f-sub .email{width:195px;background:var(--white);color:#888}
.f-sub .go{background:var(--blue-dark);color:var(--white)}
.f-rule{position:absolute;left:95px;top:266px;width:1010px;height:1px;background:var(--footer-line)}
.copyright{position:absolute;top:300px;width:1200px;text-align:center;font-size:12px}
</style>
</head>
<body>

<header class="section hero">
  <div class="hero-photo" role="img" aria-label="Smiling installer in hard hat and safety vest kneeling beside rooftop solar panels under a blue sky"></div>
  <div class="hero-shade"></div>
  <nav class="nav">
    <div class="logo"><span class="logo-mark"></span><span class="logo-name">BRIGHTFIELD</span></div>
    <div class="nav-links">
      <a class="active" style="left:22px">Home</a>
      <a style="left:112px">Services</a>
      <a style="left:214px">Products</a>
      <a style="left:320px">About Us</a>
      <a style="left:390px;left:392px">Contact Us</a>
      <span class="btn-login">Login</span>
    </div>
    <div class="social"><span></span><span></span></div>
    <div class="nav-rule"></div>
  </nav>
  <div class="play"><svg width="24" height="26" viewBox="0 0 24 26"><path d="M2 1L23 13L2 25Z" fill="#fff"/></svg></div>
  <h1 class="hero-title">Brightfield Energy</h1>
  <p class="hero-sub">Neque porro quisquam est qui dolorem</p>
  <div class="dots"><span class="on"></span><span></span><span></span><span></span><span></span></div>
</header>

<section class="section services">
  <h2 class="section-title">Our Services</h2>
  <div class="service" style="left:133px">
    <div class="service-icon"><div>
      <svg width="56" height="50" viewBox="0 0 56 50" fill="var(--green)"><rect x="6" y="2" width="44" height="32" rx="2"/><path d="M6 13H50M6 24H50M20 2V34M35 2V34" stroke="#fff" stroke-width="3"/><rect x="25" y="34" width="6" height="10"/><rect x="14" y="44" width="28" height="4"/></svg>
    </div></div>
    <h3>Quisquam</h3>
    <p>It has survived not only five centuries,<br>but also the leap into electronic</p>
  </div>
  <div class="service" style="left:451px">
    <div class="service-icon"><div>
      <svg width="56" height="56" viewBox="0 0 56 56" fill="none" stroke="var(--green)" stroke-width="4"><circle cx="28" cy="28" r="16"/><path d="M28 4V12M28 44V52M4 28H12M44 28H52M11 11L17 17M39 39L45 45M45 11L39 17M17 39L11 45"/><path d="M21 34Q22 21 35 21Q34 34 21 34Z" fill="var(--green)" stroke="none"/></svg>
    </div></div>
    <h3>Dolorem</h3>
    <p>It has survived not only five centuries,<br>but also the leap into electronic</p>
  </div>
  <div class="service" style="left:790px">
    <div class="service-icon"><div>
      <svg width="60" height="56" viewBox="0 0 60 56" fill="var(--green)"><circle cx="30" cy="12" r="6"/><path d="M30 1V3M30 21V23M19 12H21M39 12H41M22 4L24 6M36 18L38 20M38 4L36 6M24 18L22 20" stroke="var(--green)" stroke-width="2"/><path d="M14 28H46L54 50H6Z"/><path d="M11 39H49M23 28L20 50M37 28L40 50" stroke="#fff" stroke-width="2.5"/></svg>
    </div></div>
    <h3>Consectetur</h3>
    <p>It has survived not only five centuries,<br>but also the leap into electronic</p>
  </div>
</section>

<section class="section about">
  <div class="about-frame"></div>
  <div class="about-photo" role="img" aria-label="Solar panels in front of city office towers and trees with sunlight"></div>
  <h2 class="about-title">About Brightfield Energy</h2>
  <p class="about-text">It is a long established fact that a reader will be distracted by the readable content of a page when looking at its layout. The point of using Lorem Ipsum is that it has a more-or-less normal distribution of letters, as opposed to using 'Content here, content here', making it look like readable English. Many desktop publishing packages and web page editors now use Lorem Ipsum as their default model text, and a search for 'lorem ipsum' will uncover many web sites still in their infancy.</p>
  <span class="btn-more">Read More</span>
</section>

<section class="section work">
  <h2 class="section-title">What We Do</h2>
  <article class="card" style="left:95px;width:324px">
    <div class="card-photo" role="img" aria-label="Solar panels on the tiled roof of a house" style="background:linear-gradient(180deg,#b9d3ea 0%,#2f4f7a 45%,#a4552f 100%)"></div>
    <h3>Porro quisquam</h3>
    <p>It has survived not only five centuries, but also the leap into electronic typesetting,</p>
    <a>Read More »</a>
  </article>
  <article class="card" style="left:435px;width:309px">
    <div class="card-photo" role="img" aria-label="Worker installing rows of solar panels on a flat roof" style="background:linear-gradient(180deg,#cfe0ee 0%,#3c5d88 40%,#22395c 100%)"></div>
    <h3>Dolorem ipsum</h3>
    <p>It has survived not only five centuries, but also the leap into electronic typesetting,</p>
    <a>Read More »</a>
  </article>
  <article class="card" style="left:772px;width:309px">
    <div class="card-photo" role="img" aria-label="Rows of solar panels on a rooftop in warm sunlight" style="background:linear-gradient(180deg,#f3e6d2 0%,#d9c9b8 35%,#4f6c92 70%,#2b4366 100%)"></div>
    <h3>Porro quisquam</h3>
    <p>It has survived not only five centuries, but also the leap into electronic typesetting,</p>
    <a>Read More »</a>
  </article>
</section>

<section class="section testimonials">
  <h2 class="section-title">Testimonials</h2>
  <p class="quote"><span class="qmark">“</span> It is a long established fact that a reader will be distracted by the readable content of a page when looking at its layout. The point of using Lorem Ipsum is that it has a more-or-less normal distribution of letters, as opposed to using 'Content here, content here' <span class="qmark">”</span></p>
  <svg class="arrow" style="left:508px" width="16" height="28" viewBox="0 0 16 28"><path d="M13 2L3 14L13 26" fill="none" stroke="#888" stroke-width="2.5"/></svg>
  <div class="avatar" role="img" aria-label="Portrait of the reviewing customer"></div>
  <svg class="arrow" style="left:676px" width="16" height="28" viewBox="0 0 16 28"><path d="M3 2L13 14L3 26" fill="none" stroke="#888" stroke-width="2.5"/></svg>
  <p class="author">Daniel Marsh</p>
</section>

<section class="section contact">
  <h2 class="section-title">Quick Contact</h2>
  <div class="field" style="left:157px">Name</div>
  <div class="field" style="left:465px">Number</div>
  <div class="field" style="left:774px">Address</div>
  <span class="btn-submit">Submit</span>
</section>

<footer class="section footer">
  <div class="f-col" style="left:161px">
    <h4>Contact</h4>
    <ul>
      <li><svg width="9" height="12" viewBox="0 0 9 12"><path d="M4.5 0A4.5 4.5 0 0 0 0 4.5C0 8 4.5 12 4.5 12S9 8 9 4.5A4.5 4.5 0 0 0 4.5 0Z" fill="#fff"/><circle cx="4.5" cy="4.5" r="1.6" fill="#232323"/></svg>742 Linden Ave, Fairmont, IL 60100</li>
      <li style="margin-top:8px"><svg width="11" height="11" viewBox="0 0 11 11"><path d="M2 0L4 3L3 4.5Q4.5 7 6.5 8L8 7L11 9L9.5 11Q4 10.5 0 2Z" fill="#fff"/></svg>(555) 014-2290</li>
      <li style="margin-top:8px"><svg width="12" height="9" viewBox="0 0 12 9"><rect width="12" height="9" fill="#fff"/><path d="M0 0L6 5L12 0" fill="none" stroke="#232323" stroke-width="1.2"/></svg>info@brightfieldhome.com</li>
    </ul>
  </div>
  <div class="f-col" style="left:545px">
    <h4>Information</h4>
    <ul>
      <li>» Privacy Policy</li>
      <li>» Login</li>
      <li>» Advanced Search</li>
      <li>» Contact Us</li>
    </ul>
  </div>
  <div class="f-col" style="left:792px;top:106px">
    <div class="f-social"><span></span><span></span></div>
    <p class="f-note">Neque porro quisquam est qui dolorem quia dolor sit amet, consectetur</p>
    <div class="f-sub"><div class="email">Email address</div><div class="go">Submit</div></div>
  </div>
  <div class="f-rule"></div>
  <p class="copyright">Copyright © 2017 All Rights Reserved</p>
</footer>

</body>
</html>
```